Dog Snacks brand needs a new packaging design

Dear Designers,

We are looking for a packaging expert to design our new line of Dog Snacks which contain a relaxing hemp extract (CBD).

Our company is already selling various relaxing cat & dog products , and we would like this new design to reflect the same "style & feeling" as our current products (see attached instructions).

Technical aspects:
- The packaging is a Stand Up Pouch (12x18.5x7cm - see attached instructions).
- Please follow technical guidelines from printer (see attached instructions).
- The packaging will contain 120g of high-quality, semi-moist dog snacks.
- We will be designing 3 differents variations for 3 different flavours: Chicken, Beef & Liver.
- The packaging will be printed with a matt finish.

Design aspects:
- The design should be compatible with our brand identity (i.e. fluffly, pure, relaxing, positive, clean & natural).
- Soft/rounded shapes are preferred.
- Please use our brand's colors (#3BA384, White & Black).
- Please use our company logo (see attached instructions).
- The design also needs to convey a strong sense of professionalism as we are an animal "healthcare" brand.
- If you want to include a dog picture, we would prefer you to use a picture of our official brand ambassador (see attached instructions).
- We have attached a number of packaging examples which we like a lot. (see attached instructions). Please only use those as general inspiration.
- Only original work (no plagiarism will be accepted).

Please don't hesitate to send us a message if you have any questions about the brand, the product or the design requirements.

We look forward to seeing your designs & working on this together !

Thanks & regards,
Tobias

Target Market(s)

Dog owners

Industry/Entity Type

Pet Care

Font styles to use
Sans Serif

Requirements
Must have
• Please see project description.
Nice to have
Should not have

```html
<!DOCTYPE html>
<html lang="en">
<head>
<meta charset="utf-8">
<title>Verdalis – VerdaBites CBD Treats Pouch</title>
<link rel="stylesheet" href="https://fonts.googleapis.com/css2?family=Arvo:wght@400;700&family=Montserrat:wght@400;500;600&display=swap">
<style>
  :root {
    --stage: #1e2f29;
    --brand-green: #3ba384;
    --deep-green: #2b7d62;
    --ink: #1b1f1c;
    --white: #ffffff;
    --foil-light: #f1f2f2;
    --foil-mid: #d7d9d9;
    --foil-dark: #bfc2c2;
  }
  * { box-sizing: border-box; margin: 0; padding: 0; }
  html, body { width: 1200px; height: 960px; overflow: hidden; }
  body {
    background: radial-gradient(ellipse at center, #22352f 0%, var(--stage) 70%);
    font-family: "Montserrat", sans-serif;
    color: var(--ink);
    position: relative;
  }
  .pouch {
    position: absolute;
    left: 365px; top: 95px;
    width: 476px; height: 771px;
    border-radius: 26px 26px 4px 4px;
    background: linear-gradient(100deg, var(--foil-dark) 0%, var(--foil-light) 30%, var(--white) 50%, var(--foil-light) 68%, var(--foil-mid) 100%);
    overflow: hidden;
  }
  .zipper {
    position: absolute; left: 0; right: 0; top: 139px;
    height: 3px; background: rgba(0,0,0,0.08);
  }
  .brand-dot {
    position: absolute; left: 50%; top: 180px;
    width: 56px; height: 56px; margin-left: -28px;
    border-radius: 50%; background: var(--brand-green);
  }
  .brand-name {
    position: absolute; left: 0; right: 0; top: 248px;
    text-align: center;
    font-family: "Arvo", serif; font-weight: 700;
    font-size: 52px; letter-spacing: 1px; color: var(--ink);
  }
  .brand-sub {
    position: absolute; right: 93px; top: 310px;
    font-family: "Arvo", serif; font-weight: 400;
    font-size: 19px; color: var(--deep-green);
  }
  .product-name {
    position: absolute; left: 0; right: 0; top: 338px;
    text-align: center; font-weight: 600;
    font-size: 30px; letter-spacing: 1.5px;
    font-variant: small-caps; color: var(--deep-green);
  }
  .product-name sup { font-size: 11px; vertical-align: 16px; }
  .product-type {
    position: absolute; left: 0; right: 0; top: 372px;
    text-align: center; font-weight: 500;
    font-size: 27px; letter-spacing: 1.5px; color: var(--ink);
  }
  .dose-pill {
    position: absolute; left: 128px; top: 412px;
    width: 220px; height: 21px; border-radius: 3px;
    background: var(--deep-green); color: var(--white);
    font-size: 13px; font-weight: 500; letter-spacing: 1px;
    display: flex; align-items: center; justify-content: center;
  }
  .benefits {
    position: absolute; left: 0; right: 0; top: 446px;
    text-align: center; font-size: 12px; font-weight: 500;
    letter-spacing: 1.2px; color: var(--ink);
  }
  .flavour-badge {
    position: absolute; left: 91px; top: 486px;
    width: 152px; height: 152px; border-radius: 50%;
    background: radial-gradient(circle at 50% 40%, #4eae8f 0%, var(--deep-green) 100%);
    color: var(--white); text-align: center;
  }
  .flavour-badge::before {
    content: ""; position: absolute; inset: 7px;
    border: 1px dashed rgba(255,255,255,0.75); border-radius: 50%;
  }
  .flavour-name {
    position: absolute; left: 0; right: 0; top: 80px;
    font-size: 17px; font-weight: 600; letter-spacing: 1.5px;
  }
  .flavour-rule {
    position: absolute; left: 40px; right: 40px; top: 104px;
    height: 1px; background: rgba(255,255,255,0.8);
  }
  .net-weight {
    position: absolute; left: 0; right: 0; top: 110px;
    font-size: 17px; font-weight: 400; letter-spacing: 1.5px;
  }
  .endorsement {
    position: absolute; left: 60px; width: 210px; top: 651px;
    text-align: center; line-height: 1.05;
  }
  .endorsement .lead { font-size: 12px; font-variant: small-caps; letter-spacing: 1px; font-size: 13px; }
  .endorsement .who { font-size: 11px; font-weight: 600; letter-spacing: 1px; }
  .ambassador-photo {
    position: absolute; left: 136px; top: 473px;
    width: 337px; height: 250px;
    border-radius: 120px 120px 0 0;
    background: linear-gradient(180deg, #d2cfcc 0%, #ebe8e5 60%, #f3f1ef 100%);
  }
  .base-band {
    position: absolute; left: 0; right: 0; bottom: 0; height: 53px;
    background: var(--deep-green);
  }
</style>
</head>
<body>
  <main class="pouch">
    <div class="zipper"></div>
    <div class="brand-dot"></div>
    <div class="brand-name">VERDALIS</div>
    <div class="brand-sub">For Animals</div>
    <div class="product-name">VerdaBites<sup>TM</sup></div>
    <div class="product-type">CBD TREATS</div>
    <div class="dose-pill">CBD 250MG | 0% THC</div>
    <div class="benefits">SUPPORT | CALM | EASE</div>
    <div class="ambassador-photo" role="img" aria-label="Photo of the brand ambassador, a cream-coloured puppy with a bow tie, paws resting on the bottom band"></div>
    <div class="flavour-badge">
      <div class="flavour-name">CHICKEN</div>
      <div class="flavour-rule"></div>
      <div class="net-weight">120G</div>
    </div>
    <div class="endorsement">
      <div class="lead">Recommended by</div>
      <div class="who">VETERINARIANS</div>
    </div>
    <div class="base-band"></div>
  </main>
</body>
</html>
```